"Harbor Builders" is a residential building company and needs a new business card design and may re

We would like a redesign based on the existing logo, and would like to see a new font as well. We are bespoke home builders who build sustainable energy efficient homes.

Industry/Entity Type

Construction

Contact Information for Business Card

Business card size 40mm x 90mm

Colors

Designer to choose colors to be used in the design.

```html
<!DOCTYPE html>
<html lang="en">
<head>
<meta charset="utf-8">
<title>Harbor Builders — Business Card</title>
<link rel="stylesheet" href="https://fonts.googleapis.com/css2?family=Roboto:wght@400;500&family=Roboto+Condensed:wght@700&family=Open+Sans:wght@400;600&display=swap">
<style>
  :root {
    --backdrop: #2b2b2b;
    --lime: #bed631;
    --ink: #1c1c1c;
    --ink-soft: #3b3f2c;
    --paper: #f1f1f1;
    --url-grey: #555555;
  }
  * { margin: 0; padding: 0; box-sizing: border-box; }
  html, body {
    width: 1200px;
    height: 960px;
    overflow: hidden;
    background: var(--backdrop);
  }
  .card {
    position: absolute;
    width: 600px;
    height: 343px;
  }
  .card--front {
    left: 302px;
    top: 129px;
    background: var(--lime);
  }
  .card--back {
    left: 299px;
    top: 488px;
    background: var(--paper);
  }
  .contact {
    position: absolute;
    right: 34px;
    top: 120px;
    text-align: right;
    font-family: "Roboto", sans-serif;
    color: var(--ink-soft);
    font-size: 14px;
    line-height: 18px;
  }
  .contact__name {
    font-family: "Roboto Condensed", sans-serif;
    font-weight: 700;
    font-size: 21px;
    line-height: 26px;
    color: var(--ink);
    margin-bottom: 12px;
  }
  .contact__company { font-weight: 500; }
  .contact__block { margin-bottom: 4px; }
  .contact__line {
    display: flex;
    justify-content: flex-end;
    align-items: center;
    gap: 7px;
    height: 19px;
  }
  .contact__line svg { width: 13px; height: 13px; fill: var(--ink); flex: none; }
  .contact__reach { margin-top: 6px; }
  .brand {
    position: absolute;
    left: 0;
    right: 0;
    top: 128px;
    display: flex;
    justify-content: center;
    align-items: center;
    gap: 18px;
  }
  .brand__mark {
    width: 40px;
    height: 40px;
    background: var(--lime);
  }
  .brand__name {
    font-family: "Open Sans", sans-serif;
    font-weight: 600;
    font-size: 42px;
    color: var(--ink);
    letter-spacing: -0.5px;
  }
  .back__url {
    position: absolute;
    left: 0;
    right: 0;
    top: 297px;
    text-align: center;
    font-family: "Open Sans", sans-serif;
    font-size: 14px;
    letter-spacing: 3px;
    color: var(--url-grey);
  }
</style>
</head>
<body>
  <section class="card card--front">
    <div class="contact">
      <p class="contact__name">DANIEL FERNHURST</p>
      <div class="contact__block">
        <p class="contact__company">Harbor Builders Pty Ltd</p>
        <p>PO Box 4172 Northgate</p>
        <p>LPO Ridgeview WA 6071</p>
      </div>
      <p>Registration 48317</p>
      <p>ABN: 42 905 316 778</p>
      <div class="contact__reach">
        <p class="contact__line">0491 270 638
          <svg viewBox="0 0 16 16" aria-hidden="true"><path d="M4 0h8a1.5 1.5 0 0 1 1.5 1.5v13A1.5 1.5 0 0 1 12 16H4a1.5 1.5 0 0 1-1.5-1.5v-13A1.5 1.5 0 0 1 4 0zm0 2v11h8V2z"/></svg>
        </p>
        <p class="contact__line">daniel@harborbuilders.com.au
          <svg viewBox="0 0 16 16" aria-hidden="true"><path d="M1 3h14v10H1zm1.5 1.5L8 9l5.5-4.5z"/></svg>
        </p>
        <p class="contact__line">www.harborbuilders.com.au
          <svg viewBox="0 0 16 16" aria-hidden="true"><path d="M8 1a7 7 0 1 0 0 14A7 7 0 0 0 8 1zm-1 3 2 1-1 2-2-1zm3 4 2 1-2 3-1-2z"/></svg>
        </p>
      </div>
    </div>
  </section>

  <section class="card card--back">
    <div class="brand">
      <span class="brand__mark" aria-hidden="true"></span>
      <span class="brand__name">Harbor Builders</span>
    </div>
    <p class="back__url">www.harborbuilders.com.au</p>
  </section>
</body>
</html>
```